Cleaning service website design

We need a new nice web design(logo will be the same) for a new cleaning service Company:

Informations about Company and logo you can take from flyers in attachments.

This is a cleaning service Company which have simple rules and we would like to show that(in checklist form) on website:

- What we do and that we're Cleaning Green

- Why us?

- How much(our pricing is simple)

Also we would like to communicate with clients by some nice/big pictures on website and the most important thing is our phone number and short/fast Brimtallow.

Also there should be some space for description about our Company.

Generally all information on main page can be short: about us, about service(what we do), last reviews, tips (for example: Tip of the week) and other can be some introduction to subpage where will be more information.

There will be few subpages like: About us, About our service, Photos(Before and after), Reviews , Tips, FAQ, Contact, Looking for a Job? - most of them will be just text so you can project just one example.

```html
<!DOCTYPE html>
<html lang="en">
<head>
<meta charset="utf-8">
<title>Tidy Nest – Cleaning Service</title>
<link href="https://fonts.googleapis.com/css2?family=Source+Sans+3:wght@400;600;700&family=Roboto+Condensed:wght@300;700&display=swap" rel="stylesheet">
<style>
:root{
  --green:#6cbf4a;
  --green-dark:#4f9a2c;
  --phone-blue:#1f5fa8;
  --ink:#1d1d1d;
  --muted:#8b8b8b;
  --orange:#f79400;
  --orange-light:#ffb21c;
  --footer:#2b2b2b;
  --footer-bottom:#1a1a1a;
  --rule:#d6d6d6;
  --neutral-icon:#5a5a5a;
}
*{box-sizing:border-box;margin:0;padding:0}
html,body{width:1082px;height:1200px;overflow:hidden}
body{position:relative;background:#fff;font-family:"Source Sans 3",Arial,sans-serif;color:var(--ink)}
a{color:inherit;text-decoration:none}

.site-header{position:absolute;left:0;top:0;width:1082px;height:121px;border-bottom:5px solid #eeeeee}
.brand{position:absolute;left:134px;top:34px;font-size:30px;font-weight:700;color:var(--green-dark)}
.call{position:absolute;right:136px;top:12px;text-align:right}
.call-label{font-size:13px;color:#333}
.call-label b{font-weight:700}
.call-number{display:flex;align-items:center;justify-content:flex-end;gap:6px;font-size:24px;font-weight:700;margin-top:1px}
.main-nav{position:absolute;right:136px;top:60px;display:flex;height:61px}
.main-nav a{font-family:"Roboto Condensed",Arial,sans-serif;font-weight:700;font-size:11.5px;color:#2a2a2a;padding:0 15px;line-height:52px}
.main-nav a.active{color:var(--green);background:#f2f2f2;border-bottom:5px solid var(--green)}
.main-nav a:last-child{padding-right:0}

.hero{position:absolute;left:0;top:121px;width:1082px;height:453px}
.hero-scene{position:absolute;inset:0;background:linear-gradient(180deg,#2f6fb8 0%,#6fa3d4 38%,#c9d8cf 58%,#8fae52 78%,#7a8a3a 100%)}
.hero-person{position:absolute;right:138px;top:176px;width:330px;height:277px;background:radial-gradient(ellipse at 50% 60%,#e6b59a 0%,#c98f72 45%,rgba(160,110,80,0) 75%)}
.hero-copy{position:absolute;left:135px;top:40px;color:#fff;text-shadow:0 1px 2px rgba(0,0,0,.35)}
.hero-kicker{font-size:30px;font-weight:400}
.hero-title{font-size:30px;font-weight:700;margin-top:-2px}
.hero-price{font-size:19px;font-weight:700;margin-top:4px}
.hero-price span{color:var(--orange-light)}
.checklist{list-style:none;position:absolute;left:133px;top:178px;color:#fff;font-size:14.5px;text-shadow:0 1px 2px rgba(0,0,0,.45)}
.checklist li{display:flex;align-items:center;gap:10px;height:30.5px}
.cta{position:absolute;left:134px;top:339px;width:223px;height:52px;border-radius:5px;background:linear-gradient(180deg,var(--orange-light),var(--orange));color:#fff;font-size:25px;font-weight:700;display:flex;align-items:center;justify-content:center;gap:12px;box-shadow:0 2px 4px rgba(0,0,0,.25)}
.badge{position:absolute;left:391px;top:312px;width:96px;height:96px;border-radius:50%;background:rgba(255,255,255,.35)}

.features{position:absolute;left:135px;top:602px;display:flex;gap:22px}
.card{position:relative;width:256px;height:167px;background:linear-gradient(135deg,#f2f2f2,#fff 60%,#f3f3f3);box-shadow:0 0 3px rgba(0,0,0,.18);padding:20px 21px}
.card h2{text-align:center;color:var(--green);font-size:17px;font-weight:600}
.card p{font-size:12px;color:var(--muted);line-height:21px;margin-top:8px;white-space:nowrap}
.card .more{position:absolute;left:21px;top:125px;width:54px;height:18px;background:linear-gradient(180deg,#6ec234,#3f8f1c);color:#fff;font-size:11px;font-weight:600;text-align:center;line-height:18px;border-radius:2px}
.card-art{position:absolute;right:22px;top:96px;width:58px;height:58px;border-radius:50%}

.about{position:absolute;left:134px;top:800px;width:812px;text-align:center}
.about-head{display:flex;align-items:center;gap:16px}
.about-head::before,.about-head::after{content:"";flex:1;height:4px;border-top:1px solid var(--rule);border-bottom:1px solid var(--rule)}
.about-head h2{font-family:"Roboto Condensed",Arial,sans-serif;font-weight:300;font-size:25px;color:#111}
.about p{font-size:12px;color:#777;line-height:17px;margin-top:30px}
.about p a{color:var(--green)}

.site-footer{position:absolute;left:0;top:953px;width:1082px;height:212px;background:var(--footer);color:#fff}
.footer-col{position:absolute;top:36px}
.footer-col h3{font-size:15px;font-weight:600;margin-bottom:9px}
.footer-col li{list-style:none;font-size:11px;line-height:21px;padding-left:1px}
.newsletter p{font-size:11px}
.signup{display:flex;gap:6px;margin-top:10px}
.signup-field{width:275px;height:36px;background:#fff;border-radius:2px;color:#222;font-size:11px;line-height:36px;padding-left:13px}
.signup-go{width:38px;height:36px;border-radius:3px;background:linear-gradient(180deg,var(--orange-light),var(--orange));font-size:12px;font-weight:700;text-align:center;line-height:36px}
.social{display:flex;gap:9px;margin-top:29px}
.social span{width:20px;height:20px;border-radius:2px;background:var(--neutral-icon)}
.footer-brand{position:absolute;right:136px;top:146px;font-size:20px;font-weight:700;color:var(--green)}
.footer-bottom{position:absolute;left:0;top:1165px;width:1082px;height:35px;background:var(--footer-bottom);font-size:10.5px;color:#666;line-height:35px;padding-left:135px}
</style>
</head>
<body>

<header class="site-header">
  <a class="brand" href="#">Tidy Nest</a>
  <div class="call">
    <div class="call-label"><b>Call Us</b> to arrange your cleaning on</div>
    <div class="call-number">
      <svg width="16" height="20" viewBox="0 0 16 20"><path d="M4 1 L7 5 L5 7 Q6 12 10 14 L12 12 L15 15 L12 19 Q2 15 1 4 Z" fill="#1f5fa8"/></svg>
      555-014-2290
    </div>
  </div>
  <nav class="main-nav">
    <a class="active" href="#">HOME</a><a href="#">ABOUT US</a><a href="#">OUR SERVICES</a><a href="#">PHOTOS</a><a href="#">REVIEWS</a><a href="#">TIPS</a><a href="#">CAREERS</a><a href="#">FAQ</a><a href="#">CONTACT</a>
  </nav>
</header>

<section class="hero">
  <div class="hero-scene" role="img" aria-label="Photo of wind turbines on green hills under a blue sky"></div>
  <div class="hero-person" role="img" aria-label="Photo of a relaxed woman enjoying fresh air"></div>
  <div class="hero-copy">
    <div class="hero-kicker">Affordably</div>
    <div class="hero-title">making your life Simpler!</div>
    <div class="hero-price">Imagine! House cleaning as &nbsp;low as <span>$79</span></div>
  </div>
  <ul class="checklist">
    <li><svg width="20" height="20" viewBox="0 0 20 20"><ellipse cx="10" cy="10" rx="5" ry="10" transform="rotate(40 10 10)" fill="#5cb82e"/></svg>We use quality products so your house looks and smells the way you love</li>
    <li><svg width="20" height="20" viewBox="0 0 20 20"><ellipse cx="10" cy="10" rx="5" ry="10" transform="rotate(40 10 10)" fill="#5cb82e"/></svg>Our all staff are police checked, honest trained cleaning professionals</li>
    <li><svg width="20" height="20" viewBox="0 0 20 20"><ellipse cx="10" cy="10" rx="5" ry="10" transform="rotate(40 10 10)" fill="#5cb82e"/></svg>We provide reguler, weekly, fortnightly or monthly cleaning</li>
    <li><svg width="20" height="20" viewBox="0 0 20 20"><ellipse cx="10" cy="10" rx="5" ry="10" transform="rotate(40 10 10)" fill="#5cb82e"/></svg>We are 100% Eco friendly!</li>
  </ul>
  <a class="cta" href="#">GET STARTED
    <svg width="26" height="22" viewBox="0 0 26 22"><path d="M1 7 H13 V1 L25 11 L13 21 V15 H1 Z" fill="#fff"/></svg>
  </a>
  <div class="badge" role="img" aria-label="Guarantee badge"></div>
</section>

<section class="features">
  <article class="card">
    <h2>Why Us</h2>
    <p>Lorem ipsum dolor sit amet consectetur<br>adipiscing elit duis ante ut magna<br>is a dummy text.</p>
    <a class="more" href="#">more</a>
    <div class="card-art" role="img" aria-label="Illustration of cleaning supplies" style="background:linear-gradient(135deg,#f3b731,#5b55b8)"></div>
  </article>
  <article class="card">
    <h2>Pricing</h2>
    <p>Sed ut parspatisas ante dolore ut magna<br>nisi, Aliquam vestibulum nabi<br>jane, mowla jane.</p>
    <a class="more" href="#">more</a>
    <div class="card-art" role="img" aria-label="Illustration of banknotes" style="width:72px;height:52px;top:100px;border-radius:8px;background:#7fcb4a"></div>
  </article>
  <article class="card">
    <h2>That We Are Eco</h2>
    <p>Aliquam magna nisi tortor ut aliquam elit<br>ante dolore is a standard simply<br>dummy text.</p>
    <a class="more" href="#">more</a>
    <div class="card-art" role="img" aria-label="Eco sprout icon" style="background:radial-gradient(circle,#8fd060,#4f9a2c)"></div>
  </article>
</section>

<section class="about">
  <div class="about-head"><h2>About Tidy Nest.com</h2></div>
  <p>Lorem ipsum dolor sit amet consectetur adipiscing elit duis, ante dolore ut aliquam magna tortor nisi is a simply standard dummy text for the<br>typesetting industry worldwide. You can add your own text by replaceing this dummy text.<br>Parspatisas ante dolore ut aliquam magna nisi is also a dummy text. <a href="#">Find out more.</a></p>
</section>

<footer class="site-footer">
  <div class="footer-col" style="left:134px"><h3>Quick Links</h3><ul><li>Home</li><li>About Us</li><li>About Our Service</li><li>Photos</li><li>Contact</li></ul></div>
  <div class="footer-col" style="left:298px"><h3>Useful Links</h3><ul><li>Terms of use</li><li>Privacy Policy</li><li>Help Center</li><li>Community</li><li>Login Area</li></ul></div>
  <div class="footer-col" style="left:443px"><h3>Join Our Community</h3><ul><li>Friendbook</li><li>Chirper</li><li>Linkhub</li></ul></div>
  <div class="footer-col newsletter" style="left:627px">
    <h3>SignUp For Our Monthly Newsletter</h3>
    <p>Subscribe our newsletter &amp; get the latest news &amp; updates</p>
    <div class="signup"><div class="signup-field">Email Address</div><div class="signup-go">GO</div></div>
    <div class="social"><span></span><span></span><span></span></div>
  </div>
  <div class="footer-brand">Tidy Nest</div>
</footer>
<div class="footer-bottom">© 2013 by, Tidy Nest. All Rights Reserved.</div>

</body>
</html>
```